Website development company website

ABOUT COMPANY
Hi everyone! We're a Melbourne, Australia website development company in a need of a website design that will make online store merchants want to engage our services.
We specialise exclusively in Torvista e-commerce platform (https://torvista-platform.example/). What distinguishes our business from competition is that rather than designing and building brand new websites, we offer development, support and maintenance services to established websites. Maintenance and Support are the keywords representing our business.
Our potential clients are people with broken, slow and underperforming Torvista installations who need assistance getting their websites up and making sales. Our website must pass the message that we can help, and provide quick means of making contact.
DESIGN
Overall, we're looking for a slick, clean, airy, conservative design. No need to do anything crazy, try to stick to what's "standard" in website design these days and make it easy on all of us. The website is unlikely to be updated too often so it needs to look attractive and fresh first time over and after a year, too.
Attached is our new logo, which you'll be able to take the basic idea from, the colors and fonts. Though, don't use the fonts from the logo in the website, stick to the standard widely supported fonts. Additional use of Google fonts is fine.
Don't overdo it with colors, stick to conservative basic color set and only use the colors from the log for accents like headings etc. Please, don't be tempted to use the blue and orange as background of whole blocks, other than perhaps footer. Thanks.
For the images used, I'd like to stay away from a design studio/digital agency feel and lean more towards professional support and maintenance services. I'm thinking images of content merchants doing their job. Something along the lines of "We'll be taking care of the website so that you only need to care about the business".
Some ideas I like:
http://www.plumframe-pics.example/detail/photo/portrait-of-confident-male-design-professional-royalty-free-image/572048163
http://www.plumframe-pics.example/detail/photo/designer-taking-picture-of-hat-high-res-stock-photography/839207514
http://www.plumframe-pics.example/detail/photo/woman-packaging-pottery-royalty-free-image/216684093
Images of colorful shopping bags and shopping carts are over the top and not serious enough. Instead of images matching Online Shopping, I'd try going more for Stability, Reliability, Performance.
Our existing website is http://www.bravuln.example. Please, don't take design ideas from it, but it will give you a picture of the structure of our new website and content that's going to be used initially.
If you could include a basic icon set to use throughout the website, that would be great. If the icons could match our logo (attached), it would be a big plus.
ALL PAGES
Every page must contain clearly visible phone number (1300 648 907) and a Contact Us Now button, which opens an AJAX driven popup form with Name, Email, Phone and Message to be sent through.
To start with, main menu items will be Torvista, Portfolio, Contact.
At the bottom of each page, please, include a newsletter subscription form with text Subscribe to Torvista Support and Security Updates.
For the footer, I'd like to see a logo strip with the following logos in grayscale (no need to link anywhere): Torvista, QRX, DataVane, NCB. You'll find the logos on Google Images.
Standard footer columns follow. Here, I'd like to see logos in color: Torvista Certified Developer, Torvista Ceritified Solution Provider. Again, the logos are on Google Images.
No social media logos/links necessary anywhere on the website.
...and then the copyright line.
FRONT PAGE
Large slider with images that would appeal to our target audience. Keywords here would be Torvista System Audit, Torvista Performance Optimisation, Torvista Website Emergency Recovery, Torvista Development Infrastructure Hosting. We'll have a static page created for each of these to link to.
In a corner of the slider, or on the edge, can I have an overlay with logos in color (same as footer): Torvista Certified Developer, Torvista Ceritified Solution Provider.
Underneath, a number of blocks, each with an image and teaser that we'll use to link to various pages throughout the website.
PORTFOLIO PAGE
I'm thinking a single long page with a block per client, which will contain project name, description from us and a testimonial from client. Also, each block will contain a single large screenshot. No gallery or slideshow is necessary here, just one image per project.
I'll leave the layout up to you, but try to put yourself in the shoes of a potential client reviewing our past work by simply scrolling down this one page.
CONTACT US PAGE
Separate page with the same form as above, phone number (1300 648 907), email address (support@kavreo.example), address (Suite 42, Level 3|8 Wattlebrook Lane|Fernvale Heights VIC 3999), and a grayscale Google Map.
CODING UP
Coding up into static HTML/CSS/JS is equally important as the design itself. We're a website development company, we'll be integrating the theme. We will spot any issues and we will point them out.
Coded up design must be fully responsive. Enough said.
To be able to create any content in future, we'd like one extra page coded up with samples of all themed elements, lists, forms, buttons, 2, 3, 4-column layout, alerts, icons, etc. This page does not need to be designed, only coded up.
The design will be integrated into Drupal using Twig. If possible at all, try to keep it in mind when designing and coding up, and make the integration into a Drupal theme easier for us.
GOOD LUCK!
That's it. Let me know if anything needs clarifying. So far I've had a great experience with ArtFlockly. I don't doubt some great designs will emerge. Clever ideas are highly appreciated, but also make it clear you've read and followed the points in this brief. Cheers, Tom

```html
<!DOCTYPE html>
<html lang="en">
<head>
<meta charset="utf-8">
<title>Kavreo – Torvista Support &amp; Maintenance</title>
<link href="https://fonts.googleapis.com/css2?family=Open+Sans:wght@300;400;600;700&display=swap" rel="stylesheet">
<style>
:root{
  --orange:#e97a25;
  --orange-dark:#d9691a;
  --blue:#1d5c9e;
  --ink:#222;
  --body:#555;
  --soft:#efefef;
  --rule:#dcdcdc;
  --footer:#5d5d5d;
  --footer-text:#e8e8e8;
  --white:#fff;
}
*{box-sizing:border-box;margin:0;padding:0}
html,body{width:814px;height:1200px;overflow:hidden;background:var(--white)}
body{font-family:"Open Sans",Arial,sans-serif;color:var(--body);position:relative}
.abs{position:absolute}

/* header */
.site-header{position:absolute;left:0;top:0;width:814px;height:62px;background:var(--white)}
.brand{position:absolute;left:110px;top:15px;display:flex;align-items:center;gap:7px;text-decoration:none}
.brand-mark{width:20px;height:26px;background:var(--blue)}
.brand-name{font-size:24px;font-weight:700;color:var(--blue);letter-spacing:-.5px;line-height:1}
.main-nav{position:absolute;left:306px;top:24px;display:flex;align-items:center}
.main-nav a{font-size:8.5px;color:var(--ink);text-decoration:none;margin-right:29px;line-height:20px}
.main-nav a.is-active{background:var(--orange);color:var(--white);font-weight:600;padding:0 11px;margin-right:20px}
.search{position:absolute;left:620px;top:23px;width:86px;height:22px;border:1px solid #bbb;display:flex;align-items:center;padding-left:8px;gap:5px;font-size:5.5px;color:#888;letter-spacing:.3px}

/* hero */
.hero{position:absolute;left:0;top:62px;width:814px;height:344px;overflow:hidden}
.hero-photo{position:absolute;inset:0;background:linear-gradient(100deg,#b9976d 0%,#6d86a8 24%,#3e5677 36%,#e6d6c2 52%,#e2872f 68%,#c46a22 82%,#4b3d35 100%)}
.hero-title{position:absolute;left:420px;width:265px;top:44px;text-align:center;font-weight:300;font-size:31px;line-height:38px;color:var(--white)}
.hero-dots{position:absolute;left:363px;top:315px;display:flex;gap:12px;align-items:center}
.hero-dots span{width:7px;height:7px;border-radius:50%;background:var(--white)}
.hero-dots span.is-current{width:10px;height:10px;background:transparent;border:1.5px solid var(--white)}
.partner-strip{position:absolute;left:586px;top:294px;display:flex;gap:14px;align-items:center}
.partner-strip span{font-size:10px;font-weight:700;color:var(--white)}

/* services */
.services{position:absolute;left:0;top:406px;width:814px;height:247px;background:var(--soft)}
.section-title{position:absolute;left:0;width:814px;top:17px;text-align:center;color:var(--orange);font-weight:700;font-size:12.5px;letter-spacing:.3px}
.section-rule{position:absolute;left:387px;top:38px;width:40px;height:1.5px;background:var(--orange)}
.service{position:absolute;top:66px;width:155px;height:116px;text-align:center}
.service + .service{border-left:1px solid var(--rule)}
.service svg{display:block;margin:0 auto}
.service-name{font-size:9px;color:var(--ink);line-height:12px;margin-top:8px;height:26px;display:flex;align-items:center;justify-content:center}
.service-text{font-size:6.6px;line-height:10px;margin:8px auto 0;width:138px}
.btn{display:inline-flex;align-items:center;gap:8px;background:var(--orange);color:var(--white);font-size:7.5px;font-weight:600;letter-spacing:.3px;text-decoration:none;height:22px;padding:0 12px}
.services .btn{position:absolute;left:365px;top:203px}

/* teasers */
.teasers{position:absolute;left:0;top:653px;width:814px;height:291px;background:var(--white)}
.teaser{position:absolute;top:26px;width:188px}
.teaser-media{width:188px;height:116px}
.teaser-title{font-size:10.5px;color:var(--ink);margin:19px 0 0 3px;font-weight:400}
.teaser-text{font-size:6.6px;line-height:11px;margin:8px 0 0 2px;text-align:justify;height:50px}
.teaser .btn{margin-left:4px;height:18px;padding:0 10px;font-size:7px}
.media-card{background:linear-gradient(160deg,#c9ccd3,#8a95a6 55%,#e8e8ea)}
.media-platform{background:linear-gradient(135deg,#f39a3a,#e8661a);display:flex;align-items:center;justify-content:center}
.media-platform span{color:var(--white);font-size:19px;font-weight:400}
.media-cart{background:linear-gradient(170deg,#f4f4f6,#c5c7cc 60%,#d8313b 88%)}

/* testimonial */
.testimonial{position:absolute;left:0;top:944px;width:814px;height:99px;background:var(--soft)}
.client-name{position:absolute;left:0;width:814px;top:20px;text-align:center;font-size:21px;font-weight:300;color:#333;letter-spacing:-.3px}
.quote{position:absolute;left:262px;width:290px;top:56px;text-align:center;font-size:8.3px;line-height:13px;color:#666}
.arrow{position:absolute;top:43px;width:27px;height:27px;border-radius:50%;background:var(--white);display:flex;align-items:center;justify-content:center}

/* footer */
.site-footer{position:absolute;left:0;top:1043px;width:814px;height:157px;background:var(--footer);color:var(--footer-text)}
.footer-title{position:absolute;left:110px;top:21px;font-size:7.5px;font-weight:700;color:var(--white)}
.map{position:absolute;left:110px;top:46px;width:235px;height:86px;background:linear-gradient(135deg,#f2f2f2,#dedede)}
.contact-list{position:absolute;left:360px;top:49px;list-style:none;font-size:6.6px;line-height:13px}
.contact-list li{display:flex;gap:10px;margin-bottom:7px}
.contact-list svg{flex:none;margin-top:2px}
.footer-logos{position:absolute;left:510px;top:1117px;display:flex;gap:15px;align-items:center}
.footer-logos span{font-size:11px;font-weight:700;color:#cfcfcf}
.footer-rule{position:absolute;left:510px;top:1151px;width:196px;height:1px;background:#808080}
.copyright{position:absolute;right:108px;top:1159px;font-size:5.5px;color:var(--white)}
</style>
</head>
<body>

<header class="site-header">
  <a class="brand" href="#"><span class="brand-mark"></span><span class="brand-name">Kavreo</span></a>
  <nav class="main-nav">
    <a class="is-active" href="#">Home</a>
    <a href="#">About Us</a>
    <a href="#">Services</a>
    <a href="#">Portfolio</a>
    <a href="#">Contact Us</a>
  </nav>
  <div class="search">
    <svg width="6" height="6" viewBox="0 0 10 10"><circle cx="4" cy="4" r="3" fill="none" stroke="#666" stroke-width="1.5"/><line x1="6.3" y1="6.3" x2="9" y2="9" stroke="#666" stroke-width="1.5"/></svg>
    SEARCH....
  </div>
</header>

<section class="hero">
  <div class="hero-photo" role="img" aria-label="Merchant relaxing on a couch holding a smartphone showing the store app, warm blurred living room behind"></div>
  <h1 class="hero-title">Powering your online busniess</h1>
  <div class="partner-strip">
    <span>Torvista</span><span>DataVane</span><span>NCB</span><span>QRX</span>
  </div>
  <div class="hero-dots"><span></span><span class="is-current"></span><span></span><span></span><span></span></div>
</section>

<section class="services">
  <h2 class="section-title">OUR SERVICES</h2>
  <div class="section-rule"></div>

  <div class="service" style="left:98px">
    <svg width="32" height="30" viewBox="0 0 32 30" fill="none" stroke="#e97a25" stroke-width="3">
      <circle cx="11" cy="17" r="6"/><circle cx="11" cy="17" r="2" stroke-width="2"/>
      <circle cx="24" cy="8" r="4"/><circle cx="24" cy="23" r="3.5"/>
    </svg>
    <div class="service-name">SYSTEM AUDIT</div>
    <p class="service-text">Lorem Ipsum is simply dummy text of the printing and typesetting industry. Lorem Ipsum has been the industry's</p>
  </div>
  <div class="service" style="left:252px">
    <svg width="32" height="30" viewBox="0 0 32 30" fill="none" stroke="#e97a25" stroke-width="2.5">
      <circle cx="10" cy="19" r="6"/><circle cx="22" cy="11" r="8"/><path d="M22 11l4-4M22 2v2"/>
    </svg>
    <div class="service-name">PERFORMANCE<br>OPTIMISATION</div>
    <p class="service-text">Contrary to popular belief, Lorem Ipsum is not simply random text. It has roots in a piece of classical .</p>
  </div>
  <div class="service" style="left:409px">
    <svg width="32" height="30" viewBox="0 0 32 30" fill="none" stroke="#e97a25" stroke-width="2">
      <rect x="13" y="2" width="6" height="6"/><path d="M16 8v6M5 14h22M5 14v6M16 14v6M27 14v6"/>
      <rect x="2" y="20" width="6" height="6"/><rect x="13" y="20" width="6" height="6"/><rect x="24" y="20" width="6" height="6"/>
    </svg>
    <div class="service-name">WEBSITE EMERGENCY<br>RECOVERY</div>
    <p class="service-text">There are many variations of passages of Lorem Ipsum available, but the majority have suffered.</p>
  </div>
  <div class="service" style="left:564px">
    <svg width="32" height="30" viewBox="0 0 32 30" fill="#e97a25">
      <rect x="8" y="1" width="16" height="7"/><rect x="8" y="10" width="16" height="7"/><rect x="8" y="19" width="16" height="7"/>
      <circle cx="11" cy="4.5" r="1" fill="#fff"/><circle cx="11" cy="13.5" r="1" fill="#fff"/><circle cx="11" cy="22.5" r="1" fill="#fff"/>
      <rect x="6" y="28" width="20" height="1.5"/>
    </svg>
    <div class="service-name">DEVELOPMENT<br>INFRASTRUCTURE HOSTING</div>
    <p class="service-text">Sed ut perspiciatis unde omnis iste natus error sit voluptatem accusantium doloremque laudantium.</p>
  </div>

  <a class="btn" href="#">
    <svg width="5" height="7" viewBox="0 0 5 7"><path d="M1 0.5l3 3-3 3" fill="none" stroke="#fff" stroke-width="1.4"/></svg>
    READ MORE
  </a>
</section>

<section class="teasers">
  <article class="teaser" style="left:110px">
    <div class="teaser-media media-card" role="img" aria-label="Hands paying online with a bank card at a laptop"></div>
    <h3 class="teaser-title">Why Kavreo?</h3>
    <p class="teaser-text">Fast Torvista-based online stores, built on time and to specification, backed by effective, focused support, means that our clients are among the happiest in the eCommerce world.</p>
    <a class="btn" href="#">
      <svg width="8" height="6" viewBox="0 0 8 6"><rect width="8" height="6" fill="#fff"/><path d="M0 0l4 3 4-3" fill="none" stroke="#e97a25" stroke-width="1"/></svg>
      CONTACT US
    </a>
  </article>
  <article class="teaser" style="left:314px">
    <div class="teaser-media media-platform" role="img" aria-label="Torvista platform name on an orange panel"><span>Torvista</span></div>
    <h3 class="teaser-title">Why Torvista?</h3>
    <p class="teaser-text" style="text-align:left">Torvista is the world's leading open source eCommerce platform. No other open-source or free system offers out-of-the-box functionality and search engine friendliness comparable to Torvista CE.</p>
    <a class="btn" href="#">
      <svg width="5" height="7" viewBox="0 0 5 7"><path d="M1 0.5l3 3-3 3" fill="none" stroke="#fff" stroke-width="1.4"/></svg>
      READ MORE
    </a>
  </article>
  <article class="teaser" style="left:518px">
    <div class="teaser-media media-cart" role="img" aria-label="Small shopping cart resting on a red keyboard key"></div>
    <h3 class="teaser-title">What We Do.</h3>
    <p class="teaser-text">From support, maintenance and upgrades to redesigns, migrations and full site builds, we make your online store do what you need it to do.</p>
    <a class="btn" href="#">
      <svg width="5" height="7" viewBox="0 0 5 7"><path d="M1 0.5l3 3-3 3" fill="none" stroke="#fff" stroke-width="1.4"/></svg>
      READ MORE
    </a>
  </article>
</section>

<section class="testimonial">
  <div class="client-name">Wrenloft</div>
  <p class="quote">Bravuln are great developers whose concentration on detail does not compromise the delivery of work.</p>
  <a class="arrow" href="#" style="left:204px" aria-label="Previous">
    <svg width="6" height="9" viewBox="0 0 6 9"><path d="M5 1L1.5 4.5 5 8" fill="none" stroke="#444" stroke-width="1.2"/></svg>
  </a>
  <a class="arrow" href="#" style="left:573px" aria-label="Next">
    <svg width="6" height="9" viewBox="0 0 6 9"><path d="M1 1l3.5 3.5L1 8" fill="none" stroke="#444" stroke-width="1.2"/></svg>
  </a>
</section>

<footer class="site-footer">
  <h4 class="footer-title">CONTACT US</h4>
  <div class="map" role="img" aria-label="Grayscale street map around the office location"></div>
  <ul class="contact-list">
    <li>
      <svg width="6" height="8" viewBox="0 0 6 8"><path d="M3 0a3 3 0 0 1 3 3c0 2-3 5-3 5S0 5 0 3a3 3 0 0 1 3-3z" fill="#fff"/><circle cx="3" cy="3" r="1" fill="#5d5d5d"/></svg>
      <span>Suite 42, Level 3<br>8 Wattlebrook Lane<br>Fernvale Heights VIC 3999</span>
    </li>
    <li style="margin-top:4px">
      <svg width="8" height="8" viewBox="0 0 8 8"><path d="M1.5 0.5l1.5 2-1 1c.6 1.2 1.4 2 2.5 2.5l1-1 2 1.5-1 1.5C3.5 8 0 4.5 0 1.5z" fill="#fff"/></svg>
      <span>1300 648 907</span>
    </li>
    <li style="margin-top:4px">
      <svg width="9" height="7" viewBox="0 0 9 7"><rect width="9" height="7" fill="#fff"/><path d="M0 0l4.5 3.5L9 0" fill="none" stroke="#5d5d5d" stroke-width="1"/></svg>
      <span>support@kavreo.example</span>
    </li>
  </ul>
  <p class="copyright">Copyrights @2016 All Rights Reserved</p>
</footer>
<div class="footer-logos"><span>Torvista</span><span>DataVane</span><span>NCB</span><span>QRX</span></div>
<div class="footer-rule"></div>

</body>
</html>
```